Business Card & Email Signature Design || Upmarket + Luxury

Rima Vale Honey, a New Zealand Manuka Honey company needs a Business Card & Email Signature design.

Our logo's are attached in Gold & Black versions, feel free to be creative with how you use the logo and it's patterns in your design.

Style:
- Looking for an Elegant, Luxurious, Upmarket feel.
- Black/Matte Black Card, Gold Foil, UV Embossing

Information to Add:

- Logo
- Company Name: Rima Vale Honey
- Name: Martin Holloway
- Title: Creative Director
- Phone: +64 2815 96 417
- Email: martin@rimavalehoney.example.nz
- Website: www.rimavalehoney.example.nz

- Socials: ***For email Signature Only***
- Facebook: https://www.facebook.com/rimavalehoney/
- Instagram: https://www.instagram.com/rimavalehoney/

Target Market(s)

Asia/Europe Luxury, Upmarket

Contact Information for Business Card

- Logo
- Name: Martin Holloway
- Phone: +64 2815 96 417

Font styles to use
Other font styles liked:
• Champagne & Limousines (Attached)

Requirements
Must have
• Business Card & Email Signature Design.

Looking for a Sleek, Luxury, Upmarket Design.

```html
<!DOCTYPE html>
<html lang="en">
<head>
<meta charset="utf-8">
<title>Rima Vale Honey — Business Card</title>
<link rel="stylesheet" href="https://fonts.googleapis.com/css2?family=Montserrat:wght@400;500&family=Oswald:wght@500&display=swap">
<style>
  :root {
    --backdrop: #b8bcbd;
    --paper: #f3f2ee;
    --edge-gold: #c99a12;
    --ink: #1b1b1b;
    --text-grey: #4a4a4a;
    --rule-grey: #9a9a9a;
    --honey: #f2a900;
    --leaf: #7cb518;
  }
  * { margin: 0; padding: 0; box-sizing: border-box; }
  html, body {
    width: 1200px; height: 824px; overflow: hidden;
    background: var(--backdrop);
  }
  .canvas {
    width: 1200px; height: 824px;
    display: flex; align-items: center; justify-content: center; gap: 40px;
  }
  .card {
    width: 540px; height: 310px;
    background: var(--paper);
    border-bottom: 4px solid var(--edge-gold);
    box-shadow: 0 10px 24px rgba(0,0,0,0.18);
    position: relative;
  }

  /* Front: contact side */
  .card-front { display: flex; align-items: center; padding: 0 40px 0 44px; }
  .brand-block {
    width: 170px; display: flex; flex-direction: column; align-items: center; gap: 12px;
  }
  .brand-dot { width: 46px; height: 46px; border-radius: 50%; background: var(--honey); }
  .brand-name {
    font-family: "Montserrat", sans-serif; font-weight: 500;
    font-size: 15px; letter-spacing: 2px; text-transform: uppercase;
    color: var(--ink); text-align: center; line-height: 1.4;
  }
  .divider { width: 1px; height: 118px; background: var(--rule-grey); margin: 0 26px 0 22px; }
  .contact-block { display: flex; flex-direction: column; }
  .person-name {
    font-family: "Oswald", sans-serif; font-weight: 500;
    font-size: 27px; color: var(--honey); text-transform: uppercase; line-height: 1.1;
  }
  .person-title {
    font-family: "Montserrat", sans-serif; font-size: 14px; color: var(--leaf);
    margin-bottom: 12px;
  }
  .contact-list { list-style: none; }
  .contact-list li {
    display: flex; align-items: center; gap: 9px;
    font-family: "Montserrat", sans-serif; font-size: 12.5px; color: var(--text-grey);
    line-height: 1.75;
  }
  .contact-list svg { width: 12px; height: 12px; flex: none; fill: var(--honey); }

  /* Back: brand side */
  .card-back { display: flex; flex-direction: column; align-items: center; justify-content: center; gap: 18px; }
  .brand-dot-large { width: 60px; height: 60px; border-radius: 50%; background: var(--honey); }
  .brand-wordmark {
    font-family: "Montserrat", sans-serif; font-weight: 400;
    font-size: 30px; letter-spacing: 9px; text-transform: uppercase; color: var(--ink);
  }
</style>
</head>
<body>
<main class="canvas">
  <section class="card card-front" aria-label="Business card front">
    <div class="brand-block">
      <span class="brand-dot"></span>
      <span class="brand-name">Rima Vale Honey</span>
    </div>
    <span class="divider"></span>
    <div class="contact-block">
      <h1 class="person-name">Martin Holloway</h1>
      <p class="person-title">Creative Director</p>
      <ul class="contact-list">
        <li>
          <svg viewBox="0 0 24 24" aria-hidden="true"><path d="M6.6 10.8a15.1 15.1 0 0 0 6.6 6.6l2.2-2.2a1 1 0 0 1 1-.25 11.4 11.4 0 0 0 3.6.57 1 1 0 0 1 1 1V20a1 1 0 0 1-1 1A17 17 0 0 1 3 4a1 1 0 0 1 1-1h3.5a1 1 0 0 1 1 1c0 1.25.2 2.45.57 3.57a1 1 0 0 1-.25 1z"/></svg>
          +64 2815 96 417
        </li>
        <li>
          <svg viewBox="0 0 24 24" aria-hidden="true"><path d="M2 5h20v14H2z M3.5 6.5 12 13l8.5-6.5" fill="none" stroke="#f2a900" stroke-width="2.4"/></svg>
          martin@rimavalehoney.example.nz
        </li>
        <li>
          <svg viewBox="0 0 24 24" aria-hidden="true"><circle cx="12" cy="12" r="10"/><path d="M2 12h20M12 2c3 3 3 17 0 20M12 2c-3 3-3 17 0 20" fill="none" stroke="#f3f2ee" stroke-width="1.4"/></svg>
          www.rimavalehoney.example.nz
        </li>
      </ul>
    </div>
  </section>

  <section class="card card-back" aria-label="Business card back">
    <span class="brand-dot-large"></span>
    <p class="brand-wordmark">Rima Vale Honey</p>
  </section>
</main>
</body>
</html>
```